Upscale business cards needed for Board of Directors

We need professional business cards created for members of our family business Board of Directors. We would like these relatively simple and straightforward, but also with a unique element to set them apart. Probably stick with neutral and simple colors - white, grey etc. We need space for the traditional elements, including name, title, address, email/phone number. And we will be creating several from this template so it needs to be template that is easy to switch information in and out of.
Business
See description

```html
<!DOCTYPE html>
<html lang="en">
<head>
<meta charset="utf-8">
<title>Harborline Holdings – Business Cards</title>
<link rel="stylesheet" href="https://fonts.googleapis.com/css2?family=Source+Sans+3:wght@400;600;800&display=swap">
<style>
  :root {
    --backdrop: #5b5b5b;
    --card: #ffffff;
    --ink: #231f20;
    --gold: #a89168;
    --muted: #7a7a7a;
    --rule: #c9b893;
  }
  * { margin: 0; padding: 0; box-sizing: border-box; }
  html, body { width: 1200px; height: 1000px; overflow: hidden; }
  body {
    background: var(--backdrop);
    font-family: "Source Sans 3", sans-serif;
    position: relative;
  }
  .card {
    position: absolute;
    left: 287px;
    width: 626px;
    height: 357px;
    background: var(--card);
    box-shadow: 0 3px 8px rgba(0,0,0,0.35);
  }
  .card-front { top: 140px; }
  .card-back { top: 531px; height: 358px; }

  .wordmark {
    position: absolute;
    text-align: center;
    color: var(--ink);
    font-weight: 800;
    line-height: 1;
  }
  .wordmark .name-main { display: block; letter-spacing: 0.5px; }
  .wordmark .name-sub { display: block; letter-spacing: 0.3em; }

  .card-front .wordmark { left: 0; right: 0; top: 140px; }
  .card-front .name-main { font-size: 50px; }
  .card-front .name-sub { font-size: 25px; margin-top: 6px; padding-left: 0.3em; }

  .front-url {
    position: absolute;
    left: 0; right: 0; top: 308px;
    text-align: center;
    font-size: 14px;
    color: var(--muted);
  }

  .card-back .wordmark { left: 30px; width: 270px; top: 145px; }
  .card-back .name-main { font-size: 39px; }
  .card-back .name-sub { font-size: 20px; margin-top: 5px; padding-left: 0.3em; }

  .divider {
    position: absolute;
    left: 312px; top: 108px;
    width: 1px; height: 143px;
    background: var(--rule);
  }
  .contact {
    position: absolute;
    left: 338px; top: 104px;
    color: var(--muted);
    font-size: 14px;
    line-height: 18px;
  }
  .person-name { color: var(--gold); font-weight: 600; font-size: 18px; line-height: 22px; }
  .person-title { margin-bottom: 10px; }
  .contact-line { display: flex; align-items: center; gap: 6px; }
  .contact-line svg { width: 11px; height: 11px; flex: none; margin-left: -1px; }
  .address { margin-top: 9px; }
</style>
</head>
<body>
  <section class="card card-front">
    <div class="wordmark">
      <span class="name-main">HARBORLINE</span>
      <span class="name-sub">HOLDINGS</span>
    </div>
    <p class="front-url">www.harborlineholdings.com</p>
  </section>

  <section class="card card-back">
    <div class="wordmark">
      <span class="name-main">HARBORLINE</span>
      <span class="name-sub">HOLDINGS</span>
    </div>
    <div class="divider"></div>
    <div class="contact">
      <p class="person-name">Daniel Reyes</p>
      <p class="person-title">President</p>
      <p class="contact-line">
        <svg viewBox="0 0 12 12" aria-hidden="true"><rect x="3" y="0.5" width="6" height="11" rx="1.2" fill="none" stroke="#a89168" stroke-width="1.2"/><circle cx="6" cy="9.5" r="0.7" fill="#a89168"/></svg>
        012-555-0147
      </p>
      <p class="contact-line">
        <svg viewBox="0 0 12 12" aria-hidden="true"><rect x="1" y="2.5" width="10" height="7" fill="#a89168"/><path d="M1 2.5 L6 6.5 L11 2.5" fill="none" stroke="#fff" stroke-width="0.9"/></svg>
        info@harborlineholdings.com
      </p>
      <p class="contact-line">
        <svg viewBox="0 0 12 12" aria-hidden="true"><circle cx="6" cy="6" r="4.5" fill="#a89168"/><path d="M1.5 6 H10.5 M6 1.5 V10.5" stroke="#fff" stroke-width="0.7"/></svg>
        www.harborlineholdings.com
      </p>
      <p class="address">Street name, Suite 100 State,<br>Zip Code, Country</p>
    </div>
  </section>
</body>
</html>
```